Tech business card design

We need an amazing business card design for our new business 'Pexla' a marketing tech startup based in Sydney, Australia. We provide an online marketplace for businesses to search and buy advertising media, connect with service providers and learn more about marketing. We wish to communicate 'cool tech', reliability and professionalism and design based around our logo.

Target Market(s)

Business Owners

Contact Information for Business Card

Name
Position
Email Address
Website
Phone Number

Font styles to use
Other font styles liked:
• Avenir & Avenir Next

Colors

Designer to choose colors to be used in the design.

```html
<!DOCTYPE html>
<html lang="en">
<head>
<meta charset="utf-8">
<title>Pexla Business Card</title>
<link rel="stylesheet" href="https://fonts.googleapis.com/css2?family=Nunito+Sans:wght@400;700;900&display=swap">
<style>
  :root {
    --page-bg: #2b2b2b;
    --card-white: #ffffff;
    --card-grey: #6d6e71;
    --navy: #1b1a4a;
    --band-grey: #8f9093;
    --ink: #1e1e1e;
    --rule: #c9c9c9;
  }
  * { margin: 0; padding: 0; box-sizing: border-box; }
  html, body {
    width: 1200px;
    height: 900px;
    overflow: hidden;
    background: var(--page-bg);
    font-family: "Nunito Sans", "Avenir Next", Avenir, sans-serif;
  }
  .canvas {
    position: relative;
    width: 1200px;
    height: 900px;
  }
  .card {
    position: absolute;
    left: 335px;
    width: 530px;
    height: 303px;
    border-radius: 24px;
    overflow: hidden;
  }
  .card-front { top: 118px; background: var(--card-white); }
  .card-back { top: 479px; background: var(--card-grey); }

  .front-swoosh {
    position: absolute;
    inset: 0;
    width: 100%;
    height: 100%;
  }
  .brand-name {
    position: absolute;
    color: var(--navy);
    font-weight: 900;
    letter-spacing: -2px;
    line-height: 1;
  }
  .card-front .brand-name {
    left: 150px;
    top: 22px;
    font-size: 100px;
  }
  .card-back .brand-name {
    left: 0;
    right: 0;
    top: 92px;
    text-align: center;
    font-size: 120px;
  }

  .person {
    position: absolute;
    right: 290px;
    top: 148px;
    text-align: right;
    color: var(--ink);
  }
  .person-name {
    font-size: 16px;
    font-weight: 700;
    letter-spacing: 0.4px;
  }
  .person-role {
    font-size: 13px;
    font-weight: 700;
  }
  .address {
    margin-top: 14px;
    font-size: 13px;
    line-height: 1.2;
  }
  .divider {
    position: absolute;
    left: 254px;
    top: 140px;
    width: 1px;
    height: 82px;
    background: var(--rule);
  }
  .contact-list {
    position: absolute;
    left: 266px;
    top: 142px;
    list-style: none;
    font-size: 13px;
    color: var(--ink);
  }
  .contact-list li {
    display: flex;
    align-items: center;
    gap: 5px;
    height: 19px;
  }
  .contact-icon { width: 11px; height: 11px; fill: var(--ink); }
</style>
</head>
<body>
<main class="canvas">

  <section class="card card-front" aria-label="Business card front">
    <svg class="front-swoosh" viewBox="0 0 530 303" preserveAspectRatio="none" aria-hidden="true">
      <path d="M0,252 C90,258 190,252 320,236 C200,262 90,282 20,303 L0,303 Z" fill="var(--band-grey)"/>
      <path d="M30,303 C150,270 330,250 530,172 L530,192 C350,262 170,284 60,303 Z" fill="var(--navy)"/>
      <path d="M330,250 C400,238 470,222 530,200 C470,226 400,244 330,250 Z" fill="var(--band-grey)"/>
    </svg>

    <div class="brand-name">Pexla</div>

    <div class="person">
      <p class="person-name">JOHN SMITH</p>
      <p class="person-role">Position</p>
      <p class="address">Street Name, City Name<br>Zipcode:012345</p>
    </div>

    <div class="divider"></div>

    <ul class="contact-list">
      <li>
        <svg class="contact-icon" viewBox="0 0 24 24" aria-hidden="true"><path d="M6.6 10.8a15 15 0 0 0 6.6 6.6l2.2-2.2c.3-.3.7-.4 1-.2 1.1.4 2.3.6 3.6.6.6 0 1 .4 1 1V20c0 .6-.4 1-1 1A17 17 0 0 1 3 4c0-.6.4-1 1-1h3.5c.6 0 1 .4 1 1 0 1.3.2 2.5.6 3.6.1.3 0 .7-.2 1z"/></svg>
        012-345-6789
      </li>
      <li>
        <svg class="contact-icon" viewBox="0 0 24 24" aria-hidden="true"><path d="M2 5h20v14H2z M2 5l10 8 10-8" fill="none" stroke="currentColor" stroke-width="0"/><path d="M2 5h20L12 13z M2 7l10 8 10-8v12H2z"/></svg>
        info@pexla.com
      </li>
      <li>
        <svg class="contact-icon" viewBox="0 0 24 24" aria-hidden="true"><circle cx="12" cy="12" r="10"/><path d="M2 12h20M12 2c3 3 3 17 0 20M12 2c-3 3-3 17 0 20" stroke="#fff" stroke-width="1.5" fill="none"/></svg>
        www.pexla.com
      </li>
    </ul>
  </section>

  <section class="card card-back" aria-label="Business card back">
    <div class="brand-name">Pexla</div>
  </section>

</main>
</body>
</html>
```